Redesign Of Current Landing Page

I need to redesign this landing page https://www.brightlanepromo.biz/?page=landing&landing=23 (Please do not opt in because when you do it will show you the home page. Please clear your cookies before going to this url above to view the 1 page landing page.)

Please use my updated website as a reference for colors and logo.
http://sitecradlewerk.com/dh/bpq/index.html

I would like the call to action to be a button that opens into a lead form...

Button would be "Download Samples"

Target Market(s)

small business owners

Industry/Entity Type

Marketing

Number of Pages Required

1 page

Colors

Designer to choose colors to be used in the design.

Requirements
Must have
• must be full responsive on all devices
Nice to have
• must have a legitimate professional apeal to it
Should not have
• open

```html
<!DOCTYPE html>
<html lang="en">
<head>
<meta charset="utf-8">
<title>Brightlane Promo – Download Free Samples</title>
<link href="https://fonts.googleapis.com/css2?family=Raleway:wght@500;600;700&family=Roboto:wght@400;500&display=swap" rel="stylesheet">
<style>
:root{
  --navy:#0f2238;
  --navy-deep:#0a1828;
  --blue:#0a6fc2;
  --orange:#fdaa12;
  --white:#ffffff;
  --ink:#3a4048;
  --muted:#6b7078;
  --slate:#2c3340;
  --panel:#eeeeee;
  --footer:#1c1e22;
}
*{box-sizing:border-box;margin:0;padding:0}
html,body{width:683px;height:1200px;overflow:hidden}
body{position:relative;font-family:"Roboto",sans-serif;background:var(--white);color:var(--ink)}
.abs{position:absolute}
.heading{font-family:"Raleway",sans-serif;font-weight:700}

/* buttons */
.cta{position:absolute;display:flex;align-items:center;background:var(--orange);color:var(--white);text-decoration:none;font-family:"Raleway",sans-serif;font-size:10.5px;line-height:1.05}
.cta .cta-icon{width:42px;height:100%;display:flex;align-items:center;justify-content:center;border-right:1px solid rgba(255,255,255,.35)}
.cta .cta-text{padding-left:12px}
.cta .cta-text b{display:block;font-weight:700}
.cta .cta-text span{font-weight:500}
.cta-small{font-size:7.5px;font-weight:700;height:20px;padding:0 10px 0 0}
.cta-small .cta-icon{width:22px;border:none}

/* hero */
.hero{left:0;top:0;width:683px;height:342px;background:linear-gradient(110deg,#1b2c40 0%,#12243a 45%,#0d1d30 100%)}
.topbar{left:0;top:0;width:683px;height:20px;border-bottom:1px solid rgba(255,255,255,.12);font-size:7.5px;color:var(--white)}
.topbar .contact{position:absolute;right:88px;top:6px;display:flex;gap:10px;align-items:center}
.topbar .contact span{display:flex;align-items:center;gap:3px}
.brand{display:flex;align-items:center;gap:6px;color:var(--white);font-family:"Raleway",sans-serif;font-weight:700;font-size:15px;letter-spacing:.5px}
.brand .mark{width:14px;height:14px;background:var(--blue)}
.hero-title{left:64px;top:128px;width:243px;border-top:1px solid rgba(255,255,255,.6);padding-top:8px;font-size:19px;color:var(--white);letter-spacing:.2px}
.hero-title::after{content:"";display:block;width:155px;height:1px;background:rgba(255,255,255,.6);margin-top:7px}
.hero-sub{left:63px;top:178px;width:290px;font-size:10px;line-height:13px;color:var(--white);font-family:"Raleway",sans-serif;font-weight:500}
.hero-art{left:352px;top:128px;width:256px;height:214px}

/* intro */
.col{top:368px;width:270px}
.col h2{font-size:13.5px;font-family:"Raleway",sans-serif;font-weight:600;color:var(--ink);margin-bottom:12px}
.col p{font-size:7.4px;line-height:11.7px;color:var(--muted);margin-bottom:11.7px}
.divider{left:341px;top:348px;width:1px;height:175px;background:#e3e3e3}

/* why */
.why{left:0;top:620px;width:683px;height:266px;background:linear-gradient(180deg,#273140,#1f2835)}
.why h2{position:absolute;top:26px;width:100%;text-align:center;font-size:13.5px;color:var(--white)}
.card{position:absolute;top:58px;width:86px;height:108px;background:var(--white)}
.card .card-top{height:53px;background:var(--blue);display:flex;align-items:center;justify-content:center;position:relative}
.card .card-top::after{content:"";position:absolute;left:0;bottom:-5px;width:100%;height:5px;background:linear-gradient(172deg,var(--orange) 50%,transparent 52%)}
.card p{padding:13px 6px 0;text-align:center;font-size:7.4px;line-height:10.6px;color:var(--muted)}

/* testimonial */
.testi-title{left:63px;top:913px;font-size:13.5px;font-family:"Raleway",sans-serif;font-weight:600;color:var(--ink)}
.quote{left:63px;top:946px;width:366px;height:116px;background:var(--panel)}
.quote p{position:absolute;left:53px;top:15px;width:290px;font-size:7.4px;line-height:11.7px;color:var(--muted)}
.quote .qmark{position:absolute;left:19px;top:14px;font-family:"Raleway",sans-serif;font-weight:700;font-size:40px;line-height:40px;color:var(--blue)}
.quote .tail{position:absolute;left:62px;bottom:-26px;width:0;height:0;border-left:12px solid var(--panel);border-bottom:26px solid transparent}
.author{left:137px;top:1070px;font-size:8.5px;line-height:12px}
.author b{color:var(--blue);font-weight:500;display:block}
.author span{color:var(--muted)}
.portrait{left:420px;top:904px;width:224px;height:214px;background:linear-gradient(180deg,#f4f4f4,#e2e4e7)}

/* footer */
.footer{left:0;top:1118px;width:683px;height:82px;background:var(--footer)}
.footer .brand{position:absolute;left:63px;top:18px;color:#8a8d92;font-size:12px}
.footer .brand .mark{width:11px;height:11px;background:#8a8d92}
.social{position:absolute;left:63px;top:41px;display:flex;gap:4px}
.social i{display:block;width:19px;height:19px;border:1.3px solid #8a8d92;border-radius:50%}
.legal{position:absolute;left:132px;top:44px;font-size:7.4px;line-height:11.5px;color:#8a8d92}
</style>
</head>
<body>

<header class="hero abs" role="img" aria-label="Dark blue photo of a business team at work"></header>
<div class="topbar abs">
  <div class="contact">
    <span><svg width="7" height="9" viewBox="0 0 7 9"><rect x="1" y="0" width="5" height="9" rx="1" fill="#0a8be0"/><rect x="2" y="1.2" width="3" height="5.5" fill="#fff"/></svg>1-800-555-0142</span>
    <span><svg width="9" height="9" viewBox="0 0 10 10"><circle cx="5" cy="5" r="4" fill="none" stroke="#0a8be0" stroke-width="1.4"/><path d="M5 2.6V5h2" stroke="#0a8be0" stroke-width="1.2" fill="none"/></svg>Mon-Fri : 8am-5pm PST</span>
  </div>
</div>
<div class="brand abs" style="left:64px;top:32px"><i class="mark"></i>BRIGHTLANE PROMO</div>
<a class="cta cta-small" href="#" style="left:403px;top:30px">
  <span class="cta-icon"><svg width="9" height="9" viewBox="0 0 10 10"><rect x=".5" y=".5" width="9" height="9" fill="none" stroke="#fff"/><path d="M5 2v5M3 5l2 2 2-2" stroke="#fff" fill="none"/></svg></span>
  DOWNLOAD FREE SAMPLES OF OUR INCENTIVES
</a>

<h1 class="hero-title heading abs">ATTRACT MORE CUSTOMERS</h1>
<p class="hero-sub abs">WHO SPEND MORE MONEY WITH YOUR BUSINESS MORE OFTEN USING FREE VACATION &amp; CRUISE CERTIFICATES AND OTHER INCENTIVES WITHOUT BREAKING THE BANK!</p>
<a class="cta" href="#" style="left:63px;top:234px;width:197px;height:42px">
  <span class="cta-icon"><svg width="16" height="16" viewBox="0 0 16 16"><rect x="1" y="1" width="14" height="14" fill="none" stroke="#fff" stroke-dasharray="3 2"/><path d="M8 4v6M5 7.5 8 10.5 11 7.5" stroke="#fff" stroke-width="1.4" fill="none"/></svg></span>
  <span class="cta-text"><b>DOWNLOAD FREE SAMPLES</b><span>OF OUR INCENTIVES</span></span>
</a>
<svg class="hero-art abs" viewBox="0 0 256 214" role="img" aria-label="Sample incentive certificates for cruises, cash back and hotel stays">
  <path d="M8 214 A128 128 0 0 1 248 150 L256 214 Z" fill="#0a6fc2"/>
  <rect x="40" y="10" width="200" height="190" rx="4" fill="#3d6f9c" opacity=".55"/>
</svg>

<div class="divider abs"></div>
<section class="col abs" style="left:63px">
  <h2>IMAGINE</h2>
  <p>Being able to create exciting give away promotions that will boost your sales without ever having to worry about cost.</p>
  <p>Brightlane Promo Group, Inc. provides high-perceived value promotional incentives to businesses that want to advertise an exciting Give Away that will instantly attract more customers from your existing advertising efforts.</p>
  <p>Your business can give away incentive certificates that are redeemable for luxury hotel &amp; resort stays with airfare included, cruises, cash for gas, groceries, dining and even electronic goods.</p>
</section>
<section class="col abs" style="left:356px">
  <h2>HOW CAN WE DO IT?</h2>
  <p>Being able to create exciting give away promotions that will boost your sales without ever having to worry about cost.</p>
  <p>Brightlane Promo Group, Inc. provides high-perceived value promotional incentives to businesses that want to advertise an exciting Give Away that will instantly attract more customers from your existing advertising efforts.</p>
  <p>Your business can give away incentive certificates that are redeemable for luxury hotel &amp; resort stays with airfare included, cruises, cash for gas, groceries, dining and even electronic goods.</p>
</section>
<a class="cta" href="#" style="left:243px;top:549px;width:197px;height:42px">
  <span class="cta-icon"><svg width="16" height="16" viewBox="0 0 16 16"><rect x="1" y="1" width="14" height="14" fill="none" stroke="#fff" stroke-dasharray="3 2"/><path d="M8 4v6M5 7.5 8 10.5 11 7.5" stroke="#fff" stroke-width="1.4" fill="none"/></svg></span>
  <span class="cta-text"><b>DOWNLOAD FREE SAMPLES</b><span>OF OUR INCENTIVES</span></span>
</a>

<section class="why abs" role="region" aria-label="Why offer incentives">
  <h2 class="heading">WHY OFFER INCENTIVES TO CUSTOMERS?</h2>
  <div class="card" style="left:63px"><div class="card-top"><svg width="30" height="26" viewBox="0 0 30 26" fill="#fff"><rect x="2" y="18" width="4" height="6"/><rect x="8" y="14" width="4" height="10"/><rect x="14" y="10" width="4" height="14"/><rect x="20" y="4" width="4" height="20"/><path d="M2 14 14 5l-2-2h6v6l-2-2L3 16z"/></svg></div><p>Increase Responses From Your Existing Ads</p></div>
  <div class="card" style="left:157px"><div class="card-top"><svg width="28" height="28" viewBox="0 0 28 28"><path d="M5 23 16 12" stroke="#fff" stroke-width="5" stroke-linecap="round"/><circle cx="19" cy="9" r="6" fill="#fff"/><path d="M19 9l6-6" stroke="#0a6fc2" stroke-width="4"/></svg></div><p>#1 Sales Closing Tool - Gift w/ Purchase</p></div>
  <div class="card" style="left:251px"><div class="card-top"><svg width="28" height="28" viewBox="0 0 24 24" fill="#fff"><path d="M12 1.5l3.2 6.6 7.3 1-5.3 5.1 1.3 7.2L12 18l-6.5 3.4 1.3-7.2L1.5 9.1l7.3-1z"/></svg></div><p>Build Brand Awareness and Trust</p></div>
  <div class="card" style="left:345px"><div class="card-top"><svg width="30" height="26" viewBox="0 0 30 26" fill="#fff"><circle cx="19" cy="8" r="6"/><path d="M9 26c0-7 4-10 10-10s10 3 10 10z"/><circle cx="11" cy="9" r="5" stroke="#0a6fc2" stroke-width="1.5"/><path d="M1 26c0-6 4-9 10-9s10 3 10 9z" stroke="#0a6fc2" stroke-width="1.5"/></svg></div><p>Insure The Sale Over Your Competition</p></div>
  <div class="card" style="left:439px"><div class="card-top"><svg width="30" height="24" viewBox="0 0 30 24" fill="#fff"><path d="M2 7h20V2l7 6.5-7 6.5V10H2z"/><path d="M28 17H8v-5l-7 6.5L8 25v-5h20z"/></svg></div><p>Boost Repeat and Referral Business</p></div>
  <div class="card" style="left:533px"><div class="card-top"><svg width="30" height="30" viewBox="0 0 30 30"><circle cx="15" cy="15" r="13" fill="none" stroke="#fff" stroke-width="2.4"/><circle cx="15" cy="15" r="9.5" fill="#fff"/><text x="15" y="20.5" text-anchor="middle" font-family="Roboto,sans-serif" font-weight="500" font-size="15" fill="#0a6fc2">$</text></svg></div><p>Improve Retention Rates</p></div>
  <a class="cta" href="#" style="left:243px;top:196px;width:197px;height:42px">
    <span class="cta-icon"><svg width="16" height="16" viewBox="0 0 16 16"><rect x="1" y="1" width="14" height="14" fill="none" stroke="#fff" stroke-dasharray="3 2"/><path d="M8 4v6M5 7.5 8 10.5 11 7.5" stroke="#fff" stroke-width="1.4" fill="none"/></svg></span>
    <span class="cta-text"><b>DOWNLOAD FREE SAMPLES</b><span>OF OUR INCENTIVES</span></span>
  </a>
</section>

<h2 class="testi-title abs">WHAT ABOUT OUR CLIENT SAYS</h2>
<figure class="quote abs">
  <span class="qmark">&#8220;</span>
  <p>I began using your incentives two years ago to boost lead generation efforts. I have experienced a 63% increase in lead captures. And, even more importantly, my sales have increased as well. The ability to offer unlimited certificates and not having to pay for each certificate I give away is perhaps the best feature of the program, but having the flexibility to email or print certificates for my customers is also wonderful. I even use your html banners to automate my promotions right on my website!,</p>
  <span class="tail"></span>
</figure>
<div class="author abs"><b>Dan R.</b><span>Oakridge, TN</span></div>
<div class="portrait abs" role="img" aria-label="Portrait of a smiling businessman in a grey suit with arms crossed"></div>

<footer class="footer abs">
  <div class="brand"><i class="mark"></i>BRIGHTLANE PROMO</div>
  <div class="social" aria-label="Social links"><i></i><i></i><i></i></div>
  <div class="legal">© 2017 Brightlane Promo Group, Inc. All Rights Reserved<br>Terms of Use &nbsp;|&nbsp; Privacy Policy</div>
  <a class="cta" href="#" style="left:423px;top:20px;width:197px;height:42px">
    <span class="cta-icon"><svg width="16" height="16" viewBox="0 0 16 16"><rect x="1" y="1" width="14" height="14" fill="none" stroke="#fff" stroke-dasharray="3 2"/><path d="M8 4v6M5 7.5 8 10.5 11 7.5" stroke="#fff" stroke-width="1.4" fill="none"/></svg></span>
    <span class="cta-text"><b>DOWNLOAD FREE SAMPLES</b><span>OF OUR INCENTIVES</span></span>
  </a>
</footer>

</body>
</html>
```